Business Card Design Project

I need a business card designed from scratch. I have an existing logo that I can upload in Illustrator for modification or redesign.

The Company is called Query Lanterns http://querylanterns.com.au and we provide Search Engine Optimization services to Australian businesses. The current logo signifies an increase in visitors, profits etc...

There are no restrictions as to the redesign - colours, style etc are all open to change.

Cards will be full colour and one sided printed at http://www.cardmoxel.com.au so check their requirements for file format and sizes etc.

I will expect all original files upon completion of project.

Target Market(s)

Any business with a web site looking to improve their search engine rankings

Industry/Entity Type

Business

Requirements
Must have
• I like modern, sleek designs. Clean, not fussy, uncluttered.

```html
<!DOCTYPE html>
<html lang="en">
<head>
<meta charset="utf-8">
<title>Query Lanterns – Business Card</title>
<link href="https://fonts.googleapis.com/css2?family=Source+Sans+3:wght@400;600;700;800&display=swap" rel="stylesheet">
<style>
  :root {
    --backdrop: #a67c1e;
    --card: #ffffff;
    --brand-blue: #1a72b8;
    --deep-blue: #1d5fa0;
    --brand-yellow: #f6b81c;
    --light-yellow: #f7d84a;
    --ink: #222222;
    --rule: #1a1a1a;
  }
  * { margin: 0; padding: 0; box-sizing: border-box; }
  html, body { width: 1200px; height: 686px; overflow: hidden; }
  body {
    background: var(--backdrop);
    font-family: "Source Sans 3", "Helvetica Neue", Arial, sans-serif;
    position: relative;
  }
  .card {
    position: absolute;
    width: 451px;
    height: 256px;
    background: var(--card);
    border-radius: 22px;
    overflow: hidden;
    box-shadow: 1px 2px 3px rgba(0,0,0,0.55);
  }
  .card--front { left: 100px; top: 177px; }
  .card--back  { left: 603px; top: 266px; }
  .card__bands { position: absolute; inset: 0; width: 451px; height: 256px; }

  .brand {
    position: absolute;
    left: 0; right: 0;
    display: flex;
    justify-content: center;
    align-items: center;
    gap: 10px;
    color: var(--brand-blue);
    font-weight: 800;
  }
  .brand--front { top: 54px; font-size: 34px; line-height: 1; }
  .brand__square { width: 22px; height: 22px; background: var(--brand-yellow); }

  .divider {
    position: absolute;
    left: 160px; top: 130px;
    width: 135px; height: 2px;
    background: linear-gradient(to right, transparent, var(--rule) 35%, var(--rule) 65%, transparent);
  }
  .contact {
    position: absolute;
    left: 0; right: 0;
    top: 151px;
    text-align: center;
    color: var(--ink);
    font-size: 13px;
    line-height: 19.5px;
  }
  .contact__name { font-size: 18px; font-weight: 700; color: var(--brand-blue); line-height: 22px; }
  .contact__sep { display: inline-block; width: 1px; height: 15px; background: var(--brand-blue); margin: 0 6px; vertical-align: -2px; }
  .contact__title { font-size: 13px; font-weight: 700; color: var(--brand-yellow); }
  .contact__row { display: flex; justify-content: center; align-items: center; gap: 12px; }
  .contact__item { display: inline-flex; align-items: center; gap: 3px; }
  .contact__icon { width: 11px; height: 11px; fill: var(--brand-blue); }
  .contact__web { font-weight: 700; color: var(--brand-blue); }
  .contact__web-accent { color: var(--brand-yellow); }

  .brand--back {
    top: 74px;
    flex-direction: column;
    font-size: 50px;
    line-height: 50px;
    gap: 0;
  }
</style>
</head>
<body>

<section class="card card--front" aria-label="Card front">
  <svg class="card__bands" viewBox="0 0 451 256" aria-hidden="true">
    <defs>
      <linearGradient id="sideYellow" x1="0" x2="1" y1="0" y2="0">
        <stop offset="0" stop-color="#f2a914"/>
        <stop offset="1" stop-color="#f9de55"/>
      </linearGradient>
      <linearGradient id="sideBlue" x1="1" x2="0" y1="0" y2="0">
        <stop offset="0" stop-color="#164f8c"/>
        <stop offset="1" stop-color="#2a7dc4"/>
      </linearGradient>
    </defs>
    <path d="M0,0 H24 Q9,128 24,256 H0 Z" fill="url(#sideYellow)"/>
    <path d="M451,0 H427 Q442,128 427,256 H451 Z" fill="url(#sideBlue)"/>
  </svg>

  <div class="brand brand--front">
    <span class="brand__square" aria-hidden="true"></span>
    <span class="brand__name">Query Lanterns</span>
  </div>

  <div class="divider" aria-hidden="true"></div>

  <div class="contact">
    <div><span class="contact__name">Your Name</span><span class="contact__sep"></span><span class="contact__title">Title</span></div>
    <div>Street name City, State, zip code</div>
    <div class="contact__row">
      <span class="contact__item">
        <svg class="contact__icon" viewBox="0 0 24 24" aria-hidden="true"><path d="M6.6 10.8a15.1 15.1 0 0 0 6.6 6.6l2.2-2.2a1 1 0 0 1 1-.25 11.4 11.4 0 0 0 3.6.57 1 1 0 0 1 1 1V20a1 1 0 0 1-1 1A17 17 0 0 1 3 4a1 1 0 0 1 1-1h3.5a1 1 0 0 1 1 1c0 1.25.2 2.45.57 3.57a1 1 0 0 1-.25 1z"/></svg>123-456-7890
      </span>
      <span class="contact__item">
        <svg class="contact__icon" viewBox="0 0 24 24" aria-hidden="true"><path d="M2 5h20v14H2z M2 5l10 8 10-8" fill="var(--brand-blue)" stroke="#fff" stroke-width="1.6"/></svg>inquiry@querylanterns.com.au
      </span>
    </div>
    <div class="contact__web">www.<span class="contact__web-accent">querylanterns</span>.com.au</div>
  </div>
</section>

<section class="card card--back" aria-label="Card back">
  <svg class="card__bands" viewBox="0 0 451 256" aria-hidden="true">
    <defs>
      <linearGradient id="topYellow" x1="0" x2="0" y1="0" y2="1">
        <stop offset="0" stop-color="#f4a812"/>
        <stop offset="1" stop-color="#f8e15a"/>
      </linearGradient>
      <linearGradient id="bottomBlue" x1="0" x2="0" y1="0" y2="1">
        <stop offset="0" stop-color="#2b7dc4"/>
        <stop offset="1" stop-color="#154c88"/>
      </linearGradient>
    </defs>
    <path d="M55,0 H395 Q225,46 55,0 Z" fill="url(#topYellow)"/>
    <path d="M45,256 Q225,212 405,256 Z" fill="url(#bottomBlue)"/>
  </svg>

  <div class="brand brand--back">
    <span>Query</span>
    <span>Lanterns</span>
  </div>
</section>

</body>
</html>
```